Business Card Design

We need a business card designed for our new company. Prefer a black card with white logo & writing.

Contact Information for Business Card

Ted Galloway, address: 7-4812 Fernhollow Road, Abbotsford, BC, V3K 8R2, Office Phone: 604-712-3390, Cell: 604-947-2164, Email: ted@resinworkshub.ca

Colors

Designer to choose only greyscale colors for use in the design.

```html
<!DOCTYPE html>
<html lang="en">
<head>
<meta charset="utf-8">
<title>Resinworks Hub — Business Card</title>
<link href="https://fonts.googleapis.com/css2?family=Montserrat:wght@400;700;800&display=swap" rel="stylesheet">
<style>
  :root {
    --backdrop: #262626;
    --card: #000000;
    --ink: #ffffff;
  }
  * { margin: 0; padding: 0; box-sizing: border-box; }
  html, body {
    width: 1200px; height: 900px; overflow: hidden;
    background: var(--backdrop);
    font-family: "Montserrat", sans-serif;
    color: var(--ink);
  }
  .card {
    position: absolute;
    left: 341px;
    width: 518px; height: 296px;
    background: var(--card);
  }
  .card--front { top: 141px; }
  .card--back { top: 463px; }

  .wordmark {
    position: absolute; left: 0; right: 0;
    text-align: center;
    font-weight: 800;
    letter-spacing: 0.02em;
    color: var(--ink);
    white-space: nowrap;
  }
  .card--front .wordmark { top: 78px; font-size: 29px; }
  .card--back .wordmark { top: 125px; font-size: 40px; }

  .divider { position: absolute; left: 0; top: 0; }

  .holder-name {
    position: absolute; left: 26px; top: 196px;
    font-size: 17px; font-weight: 700; letter-spacing: 0.01em;
  }
  .contact {
    position: absolute;
    font-size: 13.5px; font-weight: 400; line-height: 18px;
  }
  .contact--personal { left: 26px; top: 236px; }
  .contact--office { right: 28px; top: 199px; text-align: right; }
  .contact-row { display: flex; align-items: center; gap: 6px; height: 18px; }
  .contact--office .contact-row { justify-content: flex-end; }
  .contact-row svg { width: 12px; height: 12px; flex: none; }
  .address-line { display: block; height: 18px; }
  .address-gap { height: 2px; }
</style>
</head>
<body>

<section class="card card--front">
  <div class="wordmark">RESINWORKS HUB</div>

  <svg class="divider" width="518" height="296" viewBox="0 0 518 296" aria-hidden="true">
    <polyline points="26,188 490,188" fill="none" stroke="#fff" stroke-width="1.4"/>
    <polyline points="217,188 151,225 26,225" fill="none" stroke="#fff" stroke-width="1.4"/>
  </svg>

  <div class="holder-name">TED GALLOWAY</div>

  <div class="contact contact--personal">
    <div class="contact-row">
      <svg viewBox="0 0 12 12" aria-hidden="true"><rect x="3" y="0.7" width="6" height="10.6" rx="1" fill="none" stroke="#fff" stroke-width="1.2"/><circle cx="6" cy="9.6" r="0.6" fill="#fff"/></svg>
      <span>604-947-2164</span>
    </div>
    <div class="contact-row">
      <svg viewBox="0 0 12 12" aria-hidden="true"><rect x="0.5" y="2.5" width="11" height="7.5" fill="#fff"/><polyline points="0.5,2.8 6,6.8 11.5,2.8" fill="none" stroke="#000" stroke-width="1"/></svg>
      <span>ted@resinworkshub.ca</span>
    </div>
  </div>

  <div class="contact contact--office">
    <span class="address-line">7-4812 Fernhollow Road</span>
    <span class="address-line">Abbotsford, BC, V3K 8R2</span>
    <div class="address-gap"></div>
    <div class="contact-row">
      <span>604-712-3390</span>
      <svg viewBox="0 0 12 12" aria-hidden="true"><path d="M2.4 0.8 L4.4 0.8 L5.2 3.4 L3.9 4.4 C4.6 6 5.9 7.3 7.6 8.1 L8.6 6.8 L11.2 7.6 L11.2 9.6 C11.2 10.5 10.5 11.2 9.6 11.2 C4.8 11 1 7.2 0.8 2.4 C0.8 1.5 1.5 0.8 2.4 0.8 Z" fill="#fff"/></svg>
    </div>
    <div class="contact-row">
      <span>resinworkshub.ca</span>
      <svg viewBox="0 0 12 12" aria-hidden="true"><g fill="none" stroke="#fff" stroke-width="0.9"><circle cx="6" cy="6" r="5.3"/><ellipse cx="6" cy="6" rx="2.3" ry="5.3"/><line x1="0.7" y1="6" x2="11.3" y2="6"/><path d="M1.6 3.3 H10.4 M1.6 8.7 H10.4"/></g></svg>
    </div>
  </div>
</section>

<section class="card card--back">
  <div class="wordmark">RESINWORKS HUB</div>
</section>

</body>
</html>
```